Edgey, Modern Air Conditioning Website

Bramble Works
current website - www.kelvaroom.nz
Facebook - www.facebook.com/bramwrk

We really have no idea about webdesign etc we are Engineers not Graphic artists or creative writers. We really just want a edgy, modern website completed on our behalf

We can get pictures of projects as directed or happy for you to use stock images of Talvoro Mecha NZ (Heatpumps) air conditioning and exposed ducting etc

we would like the website to be heavily based on the below website. I like what they have done with both the site and the app but obviously would need to suit Bramble Works, snowflakes heating cooling etc etc Blue and white to match our logo etc

http://parrowbeams.co.nz/

Need links to contact page:
Bramble Works
27 Harlow Crescent
Petone
Wellington

0800 529 174 (0800BRAMWKS)

Marta.k@bramwks.co.nz

BRAMBLE WORKS
SATISFACTION GAURANTEED

WHY CHOOSE BRAMBLE WORKS
EXPERIENCE COUNTS

We have a team of nationally trained and qualified Refrigeration/HVAC/Electrical Engineers and Technicians based in Petone, Wellington offering services to Wellington, Manuwatu and the Wairarapa. We are factory trained and authorised to design, service and install all major brands including Talvoro, Pelnor, Korrowane Electric, Veltrada and Osmelo units. We extend our installation warranty to match that of the manufacturer’s warranty and specialise in our own diagnostics and repair.

SATISFACTION GUARANTEE
We aim to please and I put my name behind our brand! We will take care of your project from start to finish and offer a unique experience with our 100% satisfaction Guarantee*. We will supply and install your system and if your system is not installed how it was explained or not up to a trades standard we will return to make any the necessary modifications free of charge. We back this service up with our 0% upfront strategy, the power is in your hands. We will only invoice you once the installation has been completed up to a BRAMBLE WORKS standard.

LOW PRESSURE SALES
Nobody likes the vacuum salesmen’s techniques and neither do we. We will come to your home or business to provide a free measure and quote. Our experience will insure this is a quick and painless experience, you will be provided with expert advice from a qualified Refrigeration Engineer, not a car salesmen turned “Heating Guru”. We will follow up with an email providing our best price straight up, installation details and online brochures. We won’t bug you with repeated phone calls and inbox clogging emails. Once we receive confirmation we will issue you with an installation date and typically have your installation completed within 10 working days.

BRANDS
www.talvoromecha.co.nz
www.pelnor.co.nz
http://quellaro.co.nz/

SERVICES
Heatpumps/Air Conditioning – Heat pumps are the most efficient way of using electricity to heat your home, but some are more efficient than others. We will select the right model for your requirements taking into account the capacity required, the visual impact of the system, the style of system, air flow and obviously your personal preferences. We only install the highest quality brands that offer outstanding after sales support. Cassettes, Consoles, Under Ceilings, Ducted, Hiwalls, Multis… Confused? Give us a call.

COMMERCIAL
We have a growing Portfolio of clients that rely on us for their Commercial requirements. We have proven ourselves to be a force to be reckoned with to be able to think outside the square and come up with unique and cost effective solutions to heat and cool large areas.

CENTRAL HEATING
Ducted Heatpumps are the holy grail of central heating and guess what? They can also cool and dehumidify your home. Ducted Heatpumps are often overlooked or priced out of reach by less experienced salesmen as its not just a point and shoot approach. We pride ourselves in our work with Ducted systems, we are able to provide quick and economic quotations and can provide expert advice on all the extra options on Ducted systems with zone control, fresh air integration, positive pressure solutions. We use the best materials when it comes to insulated ducting, mounting equipment, drainage materials. Every system we design is designed with the lowest possible decibel reading, least amount of static pressure and maximum effieciency with the help of the very latest software available.

VENTILATION
Home ventilation is a very important part of insuring you have a nice dry home to maximise the efficiency of your Heat pump. Whilst HRV systems are not designed to Heat your house they are designed to keep it dry, provide fresh filtered air to ensure your home healthy and easy to heat. We offer a number of solutions from integrated ducted heatpump systems to balanced heat recovery systems and positive air systems.

TESTIMONIALS
http://www.lotbazaro.co.nz/Browse/Listing.aspx?id=415728306

Target Market(s)

Home Owners

Industry/Entity Type

Air Conditioning

Colors
33a6d7
ffffff

Requirements
Must have
• Could possibly use the 'O' from Bramble Works logo throughout website - see business Card
Nice to have
• Bright & Crisp - White and Blue
• Would love to have our Logo used throughout the website.

```html
<!DOCTYPE html>
<html lang="en">
<head>
<meta charset="utf-8">
<title>Bramble Works — Heating &amp; Air Conditioning</title>
<link href="https://fonts.googleapis.com/css2?family=Raleway:wght@400;500;600;700;800&family=Open+Sans:wght@400;600;700&display=swap" rel="stylesheet">
<style>
:root{
  --blue:#33a6d7;
  --blue-dark:#1f8fc2;
  --orange:#f5a30f;
  --ink:#333333;
  --muted:#666666;
  --line:#dddddd;
  --pale:#f3f3f3;
  --white:#ffffff;
  --black:#0b0b0b;
}
*{box-sizing:border-box;margin:0;padding:0}
html,body{width:1200px;height:3120px;overflow:hidden}
body{font-family:"Open Sans",Arial,sans-serif;color:var(--ink);background:var(--white);font-size:13px;position:relative}
.wrap{width:880px;margin:0 auto;position:relative;height:100%}
.section{position:relative;width:1200px}
.btn{display:inline-block;height:36px;line-height:36px;padding:0 16px;font-family:"Raleway",sans-serif;font-size:13px;font-weight:500;color:var(--white);border-radius:2px}
.btn-blue{background:var(--blue)}
.btn-orange{background:var(--orange)}
.section-title{display:flex;align-items:center;gap:12px;font-family:"Raleway",sans-serif;font-size:27px;font-weight:500;color:var(--ink)}
.section-title b{color:var(--blue);font-weight:700}
.ring{width:28px;height:28px;border-radius:50%;border:5px solid #9a9a9a;flex:none}
.center{justify-content:center}

/* top bar */
.topbar{height:37px;background:var(--blue);color:var(--white);font-size:11px}
.topbar .addr{position:absolute;left:0;top:11px;display:flex;gap:6px;align-items:center}
.socials{position:absolute;right:0;top:0;display:flex}
.socials span{width:30px;height:37px;display:flex;align-items:center;justify-content:center;background:var(--blue-dark);border-left:1px solid rgba(255,255,255,.15)}
.socials span i{width:10px;height:10px;border-radius:50%;background:var(--white);display:block}

/* header */
.header{height:88px;background:var(--white)}
.brand{position:absolute;left:0;top:28px;display:flex;align-items:center;gap:10px;font-family:"Raleway",sans-serif;font-weight:800;font-size:24px;color:var(--blue);letter-spacing:1px}
.brand i{width:14px;height:14px;border-radius:50%;background:var(--blue);display:block}
.nav{position:absolute;left:230px;top:36px;display:flex;gap:32px;font-family:"Raleway",sans-serif;font-size:11px;font-weight:600;color:#555}
.nav .active{color:var(--blue)}
.call{position:absolute;right:0;top:20px;text-align:right;font-family:"Raleway",sans-serif}
.call small{display:block;font-size:13px;color:#777}
.call strong{font-size:20px;color:var(--blue);font-weight:600;display:flex;align-items:center;gap:6px;justify-content:flex-end}

/* hero */
.hero{height:480px;background:linear-gradient(100deg,#3c3a36 0%,#6b6a63 35%,#a5a7a3 55%,#6c6f5d 78%,#3b4a2c 100%)}
.hero .text{position:absolute;left:0;top:155px;color:var(--white);font-family:"Raleway",sans-serif}
.hero h1{font-size:34px;font-weight:800;letter-spacing:.5px}
.hero h2{font-size:27px;font-weight:400;line-height:1.25;margin-top:2px}
.hero .actions{margin-top:14px;display:flex;gap:10px}
.dots{position:absolute;left:50%;bottom:22px;transform:translateX(-50%);display:flex;gap:5px}
.dots i{width:13px;height:13px;border-radius:50%;background:#b3b3b3;border:2px solid var(--white);display:block}
.dots i.on{background:var(--orange)}
.hero-rule{height:10px;background:var(--blue)}

/* about */
.about{height:405px}
.about .left{position:absolute;left:0;top:42px;width:460px}
.about .sub{font-family:"Raleway",sans-serif;color:var(--blue);font-size:13px;margin-top:12px}
.about p{font-size:10px;color:var(--muted);line-height:1.55;margin-top:16px}
.ticks{list-style:none;margin-top:12px}
.ticks li{display:flex;align-items:center;gap:12px;font-size:12px;color:#555;height:24px}
.ticks svg{flex:none}
.about .actions{margin-top:18px;display:flex;gap:10px}
.about .photo{position:absolute;right:0;top:48px;width:390px;height:322px;padding:6px;border:1px solid var(--line);background:var(--white)}
.about .photo div{width:100%;height:100%;background:linear-gradient(160deg,#e9e6e0 0%,#b9a48c 45%,#6e4a35 70%,#3c8ba8 100%)}

/* services */
.services{height:613px;background:var(--blue);color:var(--white)}
.services .section-title{color:var(--white);padding-top:38px}
.services .section-title b{color:var(--white)}
.services .section-title .ring{border-color:var(--white)}
.services .intro{font-size:10.5px;line-height:1.55;text-align:center;margin:18px auto 0;width:880px}
.cards{position:absolute;left:44px;top:175px;display:flex;gap:42px}
.card{position:relative;width:238px;height:340px;text-align:center}
.card svg.frame{position:absolute;left:0;top:0}
.card .body{position:absolute;left:18px;right:18px;top:162px}
.card h3{font-family:"Raleway",sans-serif;font-weight:500;font-size:18px}
.card p{font-size:10.5px;line-height:1.5;margin-top:8px}
.card .btn{position:absolute;left:50%;transform:translateX(-50%);top:293px;height:34px;line-height:34px;font-size:12px}
.confused{position:absolute;left:0;right:0;top:548px;text-align:center;font-family:"Raleway",sans-serif;font-size:21px;font-weight:500;letter-spacing:.5px}

/* why */
.why{height:360px;background:var(--pale)}
.why .section-title{padding-top:28px}
.features{position:absolute;left:40px;top:100px;width:800px;display:flex;justify-content:space-between}
.feature{width:220px;text-align:center}
.feature .icon{width:124px;height:124px;margin:0 auto;border-radius:50%;background:#e2e2e2}
.feature h4{font-family:"Raleway",sans-serif;font-weight:700;font-size:14px;line-height:1.3;margin-top:14px;color:#222}
.feature p{font-size:11px;color:var(--muted);line-height:1.5;margin-top:10px}
.link-dots{position:absolute;top:160px;left:310px;width:580px;border-top:2px dotted #bbb}

/* areas */
.areas{height:250px;border-bottom:1px solid var(--line)}
.areas .left{position:absolute;left:0;top:40px;width:280px}
.pin-row{display:flex;gap:8px;margin-top:24px}
.pin-row strong{display:block;color:var(--orange);font-family:"Raleway",sans-serif;font-weight:700;font-size:14px}
.pin-row span{font-size:13px;color:#555}
.areas hr{border:0;border-top:1px solid var(--line);margin:10px 0}
.areas p{font-size:12px;color:#555;line-height:1.55}
.areas .map{position:absolute;left:380px;top:15px;width:500px;height:220px;background:radial-gradient(ellipse at 40% 50%,#f4f4f4 0%,#e8e8e8 60%,#ffffff 100%)}

/* testimonials */
.testimonials{height:337px;background:#ececec}
.testimonials .section-title{padding-top:38px}
.quotes{position:absolute;left:0;top:100px;display:flex;gap:22px}
.quote{width:278px;height:178px;background:var(--white);padding:22px 24px;box-shadow:0 1px 3px rgba(0,0,0,.08)}
.quote p{font-size:11px;line-height:1.6;color:#444}
.who{display:flex;align-items:center;gap:12px;margin-top:18px}
.who .avatar{width:62px;height:62px;border-radius:50%;background:#c9d7df;border:3px solid var(--blue)}
.who strong{display:block;font-family:"Raleway",sans-serif;font-size:13px;color:#222}
.who strong.hl{color:var(--orange)}
.who span{font-size:11px;color:#666}

/* quick contact */
.contact{height:240px}
.contact .left{position:absolute;left:0;top:50px;width:280px}
.contact .left .section-title{font-size:22px;line-height:1.05;align-items:flex-start}
.contact .left .section-title span{display:block}
.contact .left p{font-size:11px;color:#555;line-height:1.6;margin-top:20px;width:260px}
.form{position:absolute;left:318px;top:50px;width:562px}
.form h5{font-family:"Raleway",sans-serif;font-weight:500;font-size:13px;color:#444}
.fields{display:grid;grid-template-columns:1fr 1fr;gap:12px 22px;margin-top:16px}
.fields div{height:32px;border:1px solid #cfcfcf;font-size:10px;color:#999;padding:10px 10px}
.form .btn{margin-top:14px;height:34px;line-height:34px}

/* footer */
.footer{height:238px;background:var(--black);color:var(--white)}
.footer h6{font-family:"Raleway",sans-serif;font-size:16px;font-weight:500;letter-spacing:.5px}
.footer h6 b{font-weight:800}
.links{position:absolute;left:0;top:38px}
.links ul{list-style:none;margin-top:16px}
.links li{font-size:12px;height:22px;display:flex;align-items:center;gap:10px}
.links li::before{content:"";width:5px;height:5px;border-top:1.5px solid #fff;border-right:1.5px solid #fff;transform:rotate(45deg)}
.info{position:absolute;left:218px;top:38px;width:240px}
.info .row{display:flex;gap:14px;margin-top:16px;font-size:12px;line-height:1.4;color:#ccc}
.info .row strong{color:var(--white);font-weight:400}
.footer .map{position:absolute;right:0;top:45px;width:390px;height:126px;background:linear-gradient(135deg,#e4e9dc 0%,#dfe3e6 50%,#b9d3ea 100%);border-radius:3px}
.footer .view{position:absolute;left:490px;top:184px;font-size:12px;color:#aaa}

/* bottom bar */
.bottombar{height:52px;background:var(--blue);color:var(--white);font-size:11px}
.follow{position:absolute;left:0;top:14px;display:flex;align-items:center;gap:10px}
.follow i{width:24px;height:24px;border-radius:50%;border:2px solid var(--white);display:block}
.copy{position:absolute;right:0;top:19px}
</style>
</head>
<body>

<div class="section topbar"><div class="wrap">
  <div class="addr">
    <svg width="9" height="12" viewBox="0 0 9 12"><path d="M4.5 0A4.5 4.5 0 0 0 0 4.5C0 8 4.5 12 4.5 12S9 8 9 4.5A4.5 4.5 0 0 0 4.5 0Zm0 6.3a1.8 1.8 0 1 1 0-3.6 1.8 1.8 0 0 1 0 3.6Z" fill="#fff"/></svg>
    27 Harlow Crescent, Petone, Wellington
  </div>
  <div class="socials"><span><i></i></span><span><i></i></span><span><i></i></span><span><i></i></span></div>
</div></div>

<header class="section header"><div class="wrap">
  <div class="brand"><i></i>BRAMBLE WORKS</div>
  <nav class="nav"><span class="active">HOME</span><span>ABOUT US</span><span>SERVICES</span><span>TESTIMONIALS</span><span>CONTACT US</span></nav>
  <div class="call"><small>Any Query? Call us now</small>
    <strong><svg width="16" height="16" viewBox="0 0 24 24"><path d="M6.6 10.8a15.1 15.1 0 0 0 6.6 6.6l2.2-2.2c.3-.3.7-.4 1-.2 1.1.4 2.3.6 3.6.6.6 0 1 .4 1 1V20c0 .6-.4 1-1 1A17 17 0 0 1 3 4c0-.6.4-1 1-1h3.5c.6 0 1 .4 1 1 0 1.3.2 2.5.6 3.6.1.3 0 .7-.2 1L6.6 10.8Z" fill="#33a6d7"/></svg>0 21 463 9027</strong>
  </div>
</div></header>

<section class="section hero" role="img" aria-label="Technician servicing an outdoor heat pump unit beside a brick wall">
  <div class="wrap">
    <div class="text">
      <h1>SPECIALIZING IN</h1>
      <h2>Commercial And<br>Central Heating System</h2>
      <div class="actions"><span class="btn btn-blue">Read More</span><span class="btn btn-orange">Contact Now</span></div>
    </div>
  </div>
  <div class="dots"><i></i><i class="on"></i><i></i></div>
</section>
<div class="section hero-rule"></div>

<section class="section about"><div class="wrap">
  <div class="left">
    <h2 class="section-title"><span class="ring"></span>ABOUT <b>KELVA ROOM</b></h2>
    <div class="sub">SPECIALIZING IN Commercial And Central Heating System</div>
    <p>Lorem ipsum dolor sit amet, consectetuer adipiscing elit, sed diam nonummy nibh euismod tincidunt ut laoreet dolore magna aliquam erat volutpat. Ut wisi enim ad minim veniam, quis nostrud exerci tation ullamcorper suscipit lobortis.</p>
    <ul class="ticks">
      <li><svg width="14" height="8" viewBox="0 0 14 8"><path d="M0 4h12M9 1l3 3-3 3" stroke="#33a6d7" stroke-width="1.5" fill="none"/></svg>Lorem ipsum dolor sit amet, consectetur adipiscing elit.</li>
      <li><svg width="14" height="8" viewBox="0 0 14 8"><path d="M0 4h12M9 1l3 3-3 3" stroke="#33a6d7" stroke-width="1.5" fill="none"/></svg>Aenean luctus odio congue congue viverra.</li>
      <li><svg width="14" height="8" viewBox="0 0 14 8"><path d="M0 4h12M9 1l3 3-3 3" stroke="#33a6d7" stroke-width="1.5" fill="none"/></svg>Curabitur tempor magna sed arcu finibus, sed interdum risus hendrerit.</li>
      <li><svg width="14" height="8" viewBox="0 0 14 8"><path d="M0 4h12M9 1l3 3-3 3" stroke="#33a6d7" stroke-width="1.5" fill="none"/></svg>Maecenas vulputate elit eleifend tristique pharetra.</li>
      <li><svg width="14" height="8" viewBox="0 0 14 8"><path d="M0 4h12M9 1l3 3-3 3" stroke="#33a6d7" stroke-width="1.5" fill="none"/></svg>Mauris in ante quis tellus pulvinar dignissim.</li>
    </ul>
    <div class="actions"><span class="btn btn-blue">Read More</span><span class="btn btn-orange">Contact Now</span></div>
  </div>
  <div class="photo"><div role="img" aria-label="Modern living room with exposed ceiling ducting, brick wall and sofa"></div></div>
</div></section>

<section class="section services"><div class="wrap">
  <h2 class="section-title center"><span class="ring"></span>OUR <b>SERVICES</b></h2>
  <p class="intro">Heatpumps/Air Conditioning – Heat pumps are the most efficient way of using electricity to heat your home, but some are more efficient than others. We will select the right model for your requirements taking into account the capacity required, the visual impact of the system, the style of system, air flow and obviously your personal preferences. We only install the highest quality brands that offer outstanding after sales support. Cassettes, Consoles, Under Ceilings, Ducted, Hiwalls, Multis…</p>

  <div class="cards">
    <div class="card">
      <svg class="frame" width="238" height="340" viewBox="0 0 238 340">
        <polygon points="1,110 119,20 237,110 237,339 1,339" fill="none" stroke="#fff" stroke-width="1.5"/>
        <circle cx="119" cy="78" r="74" fill="#33a6d7" stroke="#fff" stroke-width="5"/>
        <circle cx="119" cy="78" r="60" fill="#fff"/>
        <rect x="96" y="62" width="46" height="20" rx="3" fill="none" stroke="#33a6d7" stroke-width="3"/>
        <path d="M102 76h34M108 90v8M119 90v10M130 90v8" stroke="#33a6d7" stroke-width="3" stroke-linecap="round"/>
      </svg>
      <div class="body"><h3>COMMERCIAL</h3><p>We have a growing Portfolio of clients that rely on us for their Commercial requirements. We have proven ourselves to be a force to be reckoned with to be able…</p></div>
      <span class="btn btn-orange">Read More</span>
    </div>
    <div class="card">
      <svg class="frame" width="238" height="340" viewBox="0 0 238 340">
        <polygon points="1,110 119,20 237,110 237,339 1,339" fill="none" stroke="#fff" stroke-width="1.5"/>
        <circle cx="119" cy="78" r="74" fill="#33a6d7" stroke="#fff" stroke-width="5"/>
        <circle cx="119" cy="78" r="60" fill="#fff"/>
        <rect x="94" y="64" width="50" height="34" rx="4" fill="none" stroke="#33a6d7" stroke-width="3"/>
        <path d="M103 70v22M111 70v22M119 70v22M127 70v22M135 70v22M104 56q3 -4 0 -8M119 56q3 -4 0 -8M134 56q3 -4 0 -8" stroke="#33a6d7" stroke-width="2.5" fill="none" stroke-linecap="round"/>
      </svg>
      <div class="body"><h3>CENTRAL HEATING</h3><p>Ducted Heatpumps are the holy grail of central heating and guess what? They can also cool and dehumidify your home. Ducted Heatpumps are often overlooked…</p></div>
      <span class="btn btn-orange">Read More</span>
    </div>
    <div class="card">
      <svg class="frame" width="238" height="340" viewBox="0 0 238 340">
        <polygon points="1,110 119,20 237,110 237,339 1,339" fill="none" stroke="#fff" stroke-width="1.5"/>
        <circle cx="119" cy="78" r="74" fill="#33a6d7" stroke="#fff" stroke-width="5"/>
        <circle cx="119" cy="78" r="60" fill="#fff"/>
        <g fill="#33a6d7">
          <ellipse cx="119" cy="63" rx="8" ry="15"/>
          <ellipse cx="119" cy="63" rx="8" ry="15" transform="rotate(120 119 78)"/>
          <ellipse cx="119" cy="63" rx="8" ry="15" transform="rotate(240 119 78)"/>
          <circle cx="119" cy="78" r="5" fill="#fff"/>
        </g>
      </svg>
      <div class="body"><h3>VENTILATION</h3><p>Home ventilation is a very important part of insuring you have a nice dry home to maximise the efficiency of your Heat pump. Whilst HRV systems are not designed…</p></div>
      <span class="btn btn-orange">Read More</span>
    </div>
  </div>
  <div class="confused">CONFUSED? GIVE US A CALL - 0 21 463 9027</div>
</div></section>

<section class="section why"><div class="wrap">
  <h2 class="section-title center"><span class="ring"></span>WHY CHOOSE <b>BRAMBLE WORKS</b></h2>
  <div class="link-dots"></div>
  <div class="features">
    <div class="feature"><div class="icon" role="img" aria-label="Experience icon: stacked box"></div><h4>EXPERIENCE<br>COUNTS</h4><p>We have a team of nationally trained and qualified. [+]</p></div>
    <div class="feature"><div class="icon" role="img" aria-label="Guarantee icon: shield"></div><h4>SATISFACTION<br>GUARANTEE</h4><p>We aim to please and I put my name behind our brand! [+]</p></div>
    <div class="feature"><div class="icon" role="img" aria-label="Low pressure icon: snowflake"></div><h4>LOW PRESSURE<br>SALES</h4><p>We aim to please and I put my name behind our brand! [+]</p></div>
  </div>
</div></section>

<section class="section areas"><div class="wrap">
  <div class="left">
    <h2 class="section-title"><span class="ring"></span>AREAS WE <b>SERVICED</b></h2>
    <div class="pin-row">
      <svg width="14" height="19" viewBox="0 0 9 12"><path d="M4.5 0A4.5 4.5 0 0 0 0 4.5C0 8 4.5 12 4.5 12S9 8 9 4.5A4.5 4.5 0 0 0 4.5 0Zm0 6.3a1.8 1.8 0 1 1 0-3.6 1.8 1.8 0 0 1 0 3.6Z" fill="#888"/></svg>
      <div><strong>WELLINGTON</strong><span>27 Harlow Crescent, Petone, Wellington</span></div>
    </div>
    <hr>
    <p>Wellington, Masterton,<br>Palmerston North, Wanganui and<br>anywhere in between.</p>
  </div>
  <div class="map" role="img" aria-label="Outline map of the lower North Island with the Wellington service region marked"></div>
</div></section>

<section class="section testimonials" role="img" aria-label="Faded grid of client portraits behind the testimonials">
  <div class="wrap">
    <h2 class="section-title center"><span class="ring"></span>CLIENTS <b>TESTIMONIALS</b></h2>
    <div class="quotes">
      <div class="quote"><p>Lorem ipsum dolor sit amet, consectetuer adipiscing elit, sed diam nonummy nibh euismod tincidunt ut laoreet dolore .</p>
        <div class="who"><div class="avatar"></div><div><strong>Harlan Vesk</strong><span>Lorem ipsum</span></div></div></div>
      <div class="quote"><p>Lorem ipsum dolor sit amet, consectetuer adipiscing elit, sed diam nonummy nibh euismod tincidunt ut laoreet dolore .</p>
        <div class="who"><div class="avatar"></div><div><strong class="hl">Harlan Vesk</strong><span>Lorem ipsum</span></div></div></div>
      <div class="quote"><p>Lorem ipsum dolor sit amet, consectetuer adipiscing elit, sed diam nonummy nibh euismod tincidunt ut laoreet dolore .</p>
        <div class="who"><div class="avatar"></div><div><strong>Harlan Vesk</strong><span>Lorem ipsum</span></div></div></div>
    </div>
  </div>
</section>

<section class="section contact"><div class="wrap">
  <div class="left">
    <h2 class="section-title"><span class="ring"></span><div><span>QUICK</span><b>CONTACT</b></div></h2>
    <p>Duis autem vel eum iriure dolormi opl inmokl mort hendi rerit in vulpu tateml velitm essemol monop molestiel consequ ua.</p>
  </div>
  <div class="form">
    <h5>Please fill up bellow form</h5>
    <div class="fields"><div>Name</div><div>Email</div><div>Phone</div><div>Message</div></div>
    <span class="btn btn-blue">Read More</span>
  </div>
</div></section>

<footer class="section footer"><div class="wrap">
  <div class="links"><h6>QUICK <b>LINKS</b></h6>
    <ul><li>Home</li><li>About Us</li><li>Services</li><li>Testimonials</li><li>Contact Us</li></ul>
  </div>
  <div class="info"><h6>CONTACT <b>INFO</b></h6>
    <div class="row"><svg width="12" height="16" viewBox="0 0 9 12"><path d="M4.5 0A4.5 4.5 0 0 0 0 4.5C0 8 4.5 12 4.5 12S9 8 9 4.5A4.5 4.5 0 0 0 4.5 0Zm0 6.3a1.8 1.8 0 1 1 0-3.6 1.8 1.8 0 0 1 0 3.6Z" fill="#fff"/></svg><div><strong>KELVAROOM</strong><br>27 Harlow Crescent, Petone,<br>Wellington</div></div>
    <div class="row"><svg width="12" height="12" viewBox="0 0 24 24"><path d="M6.6 10.8a15.1 15.1 0 0 0 6.6 6.6l2.2-2.2c.3-.3.7-.4 1-.2 1.1.4 2.3.6 3.6.6.6 0 1 .4 1 1V20c0 .6-.4 1-1 1A17 17 0 0 1 3 4c0-.6.4-1 1-1h3.5c.6 0 1 .4 1 1 0 1.3.2 2.5.6 3.6.1.3 0 .7-.2 1L6.6 10.8Z" fill="#fff"/></svg><div>0 21 463 9027</div></div>
    <div class="row"><svg width="12" height="10" viewBox="0 0 12 10"><rect width="12" height="10" rx="1" fill="#fff"/><path d="M0 1l6 4 6-4" stroke="#0b0b0b" fill="none"/></svg><div>Marta.k@bramwks.co.nz</div></div>
  </div>
  <div class="map" role="img" aria-label="Street map of Petone with a location marker"></div>
  <div class="view">View Map</div>
</div></footer>

<div class="section bottombar"><div class="wrap">
  <div class="follow">Follow Us <i></i><i></i><i></i><i></i></div>
  <div class="copy">Copyright © 2016 Nimbara Studio. All Rights Reserved</div>
</div></div>

</body>
</html>
```